Preisliste für Kosmetikinstitut
Zielgruppe
Ich benötige für mein Kosmetikinstitut eine Preisliste für die moderne Frau, aber auch Männer. Das Design sollte mein Logo enthalten. Farben des Designkonzepts einbauen.
A4 quer zum Falten, wie ein Heft, 1. Seite Preisliste mit logo, im Innenteil dann Anwendungen
Aufgabenstellung
Minimalistisch, ästhetisch, modern, edel
Kontaktdaten auf der Rückseite
LB Hautatelier
Lotte Brenner
Lindenhang 17
83671 Waakirchen
EMail: lotte@lb-hautatelier.de
Whatsapp: 0176 284 9017

```html
<!DOCTYPE html>
<html lang="de">
<head>
<meta charset="utf-8">
<title>LB Hautatelier – Preisliste, Titelvarianten</title>
<link rel="stylesheet" href="https://fonts.googleapis.com/css2?family=Questrial&family=Cormorant+Garamond:wght@400&family=Lora:wght@400&family=Libre+Baskerville:ital,wght@1,700&family=Montserrat:wght@500&display=swap">
<style>
  :root {
    --canvas: #ffffff;
    --paper: #fcfcf6;
    --ink: #6e7a79;
    --shadow: rgba(120, 125, 140, 0.12);
  }
  * { margin: 0; padding: 0; box-sizing: border-box; }
  html, body {
    width: 1200px;
    height: 1200px;
    overflow: hidden;
    background: var(--canvas);
  }
  .sheet {
    position: relative;
    width: 1200px;
    height: 1200px;
  }
  .cover {
    position: absolute;
    width: 400px;
    height: 566px;
    background: var(--paper);
    box-shadow: 0 2px 8px var(--shadow);
  }
  .cover--a { left: 152px; top: 29px; }
  .cover--b { left: 603px; top: 29px; }
  .cover--c { left: 152px; top: 623px; }
  .cover--d { left: 603px; top: 623px; }

  .brand {
    position: absolute;
    left: 86px;
    top: 118px;
    display: flex;
    align-items: center;
    gap: 14px;
    color: var(--ink);
    font-family: "Questrial", sans-serif;
    font-size: 27px;
    letter-spacing: 0.01em;
    white-space: nowrap;
  }
  .brand__mark {
    width: 84px;
    height: 84px;
    border-radius: 50%;
    border: 2px solid var(--ink);
    flex: none;
  }

  .cover__title {
    position: absolute;
    bottom: 25px;
    writing-mode: vertical-rl;
    transform: rotate(180deg);
    color: var(--ink);
    white-space: nowrap;
    line-height: 1;
    font-weight: 400;
  }
  .cover--a .cover__title {
    left: 38px;
    font-family: "Cormorant Garamond", serif;
    font-variant: small-caps;
    font-size: 40px;
    letter-spacing: 0.02em;
  }
  .cover--b .cover__title {
    left: 54px;
    font-family: "Lora", serif;
    font-size: 38px;
    letter-spacing: 0.02em;
  }
  .cover--c .cover__title {
    left: 32px;
    bottom: 22px;
    font-family: "Libre Baskerville", serif;
    font-style: italic;
    font-weight: 700;
    font-size: 30px;
  }
  .cover--d .cover__title {
    left: 52px;
    bottom: 26px;
    font-family: "Montserrat", sans-serif;
    font-weight: 500;
    font-size: 41px;
  }
</style>
</head>
<body>
  <main class="sheet">
    <section class="cover cover--a">
      <div class="brand"><span class="brand__name">LB Hautatelier</span><span class="brand__mark"></span></div>
      <h1 class="cover__title">Price List</h1>
    </section>
    <section class="cover cover--b">
      <div class="brand"><span class="brand__name">LB Hautatelier</span><span class="brand__mark"></span></div>
      <h1 class="cover__title">Price List</h1>
    </section>
    <section class="cover cover--c">
      <div class="brand"><span class="brand__name">LB Hautatelier</span><span class="brand__mark"></span></div>
      <h1 class="cover__title">Price List</h1>
    </section>
    <section class="cover cover--d">
      <div class="brand"><span class="brand__name">LB Hautatelier</span><span class="brand__mark"></span></div>
      <h1 class="cover__title">Price List</h1>
    </section>
  </main>
</body>
</html>
```